Camp Thornbrook 2021 Magazine Design

We are for someone to design our annual magazine/newsletter. This is a print newsletter that is a total of 20 pages. It will need to be designed in a way that is easy to share with our printers. The designer will need to be someone who is creative and easy to work with.
For those interested in this project we ask that you design 4 to 6 pages for us to view. Once we select the designer we will want the rest created in a two-week time span. For those submitting a bid please include front cover, theme & dates, mission & vision, and Make the Difference.

This link will provide the layout of the newsletter https://files.parcelvault.example/doc/7qzRk2LmVt9XwPa4NbHc6DsYe3FuJg8KoTiW5rQx/edit?share=1.

This link will provide you with the pictures that are needed and a few documents https://files.parcelvault.example/folders/4TpWx8QnRb2ZyLc7MfVd5HsJ?share=1

Details:
20 pages long (including covers)
8.5 x 11

Please message me if you need any further details.

Target Market(s)

Our alumni base. Covers all ages

Requirements
Must have
• Spelled out in document
Nice to have
• Spelled out in document
Should not have
• Spelled out in document

```html
<!DOCTYPE html>
<html lang="en">
<head>
<meta charset="utf-8">
<title>Camp Thornbrook 2021 Magazine Cover</title>
<link rel="stylesheet" href="https://fonts.googleapis.com/css2?family=Rye&display=swap">
<style>
  :root {
    --rust: #a35a40;
    --pine: #3f6c42;
    --slate: #2f3440;
    --amber: #c99043;
    --sky: #93b3d6;
    --gold: #dcc043;
    --cork: #7a4a24;
    --year-ink: #e9dfcc;
    --year-edge: #6b4a2e;
  }
  html, body {
    margin: 0;
    padding: 0;
    width: 927px;
    height: 1200px;
    overflow: hidden;
    background: var(--cork);
  }
  .cover {
    position: relative;
    width: 927px;
    height: 1200px;
    overflow: hidden;
  }
  .cover-photo {
    position: absolute;
    inset: 0;
    background: linear-gradient(180deg,
      var(--rust) 0%,
      var(--pine) 20%,
      var(--cork) 27%,
      var(--slate) 40%,
      var(--cork) 51%,
      var(--amber) 62%,
      var(--slate) 75%,
      var(--sky) 86%,
      var(--gold) 100%);
  }
  .visually-hidden {
    position: absolute;
    width: 1px;
    height: 1px;
    overflow: hidden;
    clip: rect(0 0 0 0);
    white-space: nowrap;
  }
  .cover-year {
    position: absolute;
    left: 252px;
    top: 146px;
    margin: 0;
    font-family: "Rye", serif;
    font-weight: 400;
    font-size: 176px;
    line-height: 1;
    letter-spacing: -6px;
    color: var(--year-ink);
    -webkit-text-stroke: 2px var(--year-edge);
    paint-order: stroke fill;
  }
</style>
</head>
<body>
  <main class="cover">
    <div class="cover-photo" role="img" aria-label="Photograph of eight painted Camp Thornbrook year boards covered in camper signatures, arranged in two columns on a cork wall"></div>
    <h1 class="cover-year"><span class="visually-hidden">Camp Thornbrook </span>2021</h1>
  </main>
</body>
</html>
```